Webdesign für HALDEN STAHLWERK
Zielgruppe
Valkorin ist Ihr leistungsstarker und zuverlässiger Partner im Bereich Metallverarbeitung. Seit unserer Firmengründung im Jahr 2001 ist unser inhabergeführtes Unternehmen in Wiesenau bei Lindberg kontinuierlich gewachsen und beschäftigt derzeit 20 engagierte und qualifizierte Mitarbeiter.
Mit der Einweihung unserer neuen Fertigungshalle 2010 haben wir unsere Produktionsfläche auf 1.400 m2 vergrößert und können Ihnen nun einen noch umfassenderen Service anbieten.
Von der CNC-gesteuerten Teilefertigung bis zu modernsten Schweiß-, Schneid-, und Bearbeitungsanlagen – für die Realisierung Ihrer individuellen Wünsche steht uns ein innovativer Maschinenpark zur Verfügung. Wir fertigen zuverlässig und termingerecht nach Ihren Plänen oder übernehmen bei Bedarf auch die gesamte Abwicklung Ihres Projektes – alles made in germany!
Das Unternehmen spricht ausschließlich B2B Kunden an.
Die Hauptleistungsbereiche sind:
- Stahl- und Palettenbau
- Blechbearbeitung
- Edelstahlbearbeitung
- Mechanische Fertigung
Aufgabenstellung
- Mitlaufende Kontaktleiste
- Integration der Social Media Kanäle
- Sehr modernes Auftreten
- Industrielles Design
- Verlinkung zum Partnerunternehmen https://www.valkorin-beispiel.de/ias/index.html

```html
<!DOCTYPE html>
<html lang="de">
<head>
<meta charset="utf-8">
<title>Valkorin – Metallverarbeitung</title>
<link href="https://fonts.googleapis.com/css2?family=Space+Grotesk:wght@400;500;600;700&display=swap" rel="stylesheet">
<style>
:root{
  --stage:#b9b9b9;
  --ink:#2b2a1f;
  --muted:#5b5a52;
  --navy:#0b3a73;
  --olive:#2f2b19;
  --olive-card:#3a3625;
  --white:#ffffff;
}
*{box-sizing:border-box;margin:0;padding:0}
html,body{width:1200px;height:3520px;overflow:hidden}
body{background:var(--stage);font-family:"Space Grotesk",sans-serif;color:var(--ink)}
.page{position:absolute;left:97px;top:97px;width:1006px;height:3327px;background:var(--white);overflow:hidden}
.abs{position:absolute}

.header{left:0;top:0;width:1006px;height:92px;background:linear-gradient(90deg,#e9e9e9,#f3f3f3);display:flex;align-items:center;justify-content:space-between;padding:0 33px}
.brand{font-weight:700;font-size:29px;letter-spacing:-1px;color:var(--ink)}
.nav{display:flex;gap:28px;font-size:14px;font-weight:500}

.hero{left:0;top:92px;width:1006px;height:583px;background:linear-gradient(120deg,#2a2c30 0%,#3c4048 40%,#4c6c95 70%,#27313f 100%)}
.hero-kicker{left:86px;top:168px;color:#fff;font-weight:500;font-size:17px}
.hero-title{left:86px;top:205px;color:#fff;font-weight:600;font-size:42px;line-height:43px}

.band{left:0;top:675px;width:1006px;height:1146px;background:linear-gradient(160deg,#e7eef2 0%,#f4f5f5 50%,#e6edf1 100%)}

.product{top:427px;width:246px;height:347px;background:#fff;border-radius:4px;box-shadow:0 2px 10px rgba(0,0,0,.1);text-align:center}
.product .photo{margin:26px auto 0;width:190px;height:188px;background:linear-gradient(180deg,#8fb9ad,#3f9384);border-radius:2px}
.product h3{font-size:13px;font-weight:600;margin-top:40px}
.product p{font-size:13px;line-height:20px;margin-top:8px;color:var(--ink);padding:0 14px}

.btn{background:var(--navy);color:#fff;font-weight:600;font-size:13px;border-radius:3px;display:flex;align-items:center;justify-content:center;letter-spacing:.3px}
.all-products{left:380px;top:801px;width:198px;height:47px}

.service{width:364px;height:395px;background:#fff;border-radius:4px;box-shadow:0 1px 6px rgba(0,0,0,.07);overflow:hidden}
.service .photo{height:183px}
.service h3{font-weight:400;font-size:21px;margin:20px 18px 0}
.service p{font-size:13px;line-height:20px;color:var(--muted);margin:14px 18px 0}
.service .more{position:absolute;left:18px;bottom:18px;height:36px;padding:0 9px;background:#f1f2f3;border-radius:3px;color:var(--navy);font-weight:600;font-size:13px;display:flex;align-items:center;letter-spacing:.4px}

.about{left:0;top:1821px;width:1006px;height:610px;background:radial-gradient(circle at 5% 95%,#676450 0%,transparent 22%),var(--olive)}
.about h2{position:absolute;top:55px;width:100%;text-align:center;color:#fff;font-size:29px;font-weight:600}
.about-card{top:126px;width:246px;height:423px;background:var(--olive-card);border-radius:3px;overflow:hidden;color:#eee}
.about-card .photo{height:167px}
.about-card h3{font-weight:400;font-size:21px;letter-spacing:.8px;margin:22px 21px 0}
.about-card p{font-size:13px;line-height:20px;margin:14px 36px 0 21px}

.contact-bottom{left:0;top:2958px;width:1006px;height:369px;background:linear-gradient(160deg,#f2f3f3 0%,#eef1f2 60%,#e2eaee 100%)}
.contact-title{left:0;top:2482px;width:1006px;text-align:center;font-size:29px;font-weight:600}
.avatar{left:201px;top:2544px;width:92px;height:92px;border-radius:50%;background:linear-gradient(160deg,#8a7060,#3b3029)}
.contact-text{left:317px;top:2547px;width:478px;font-size:13px;line-height:20px}
.signature{left:317px;top:2615px;font-size:10px;line-height:13px}
.email{left:260px;top:2663px;width:377px;height:46px;background:#f1f1f1;border-radius:3px;font-size:13px;color:#888;display:flex;align-items:center;padding-left:14px;letter-spacing:.4px}
.send{left:643px;top:2663px;width:103px;height:46px}

.review{top:2778px;width:243px;height:228px;background:#fff;box-shadow:0 1px 8px rgba(0,0,0,.08);border-radius:3px;text-align:center;padding:28px 14px 0}
.stars{display:flex;justify-content:center;gap:3px}
.review h4{font-size:13px;font-weight:600;line-height:20px;margin-top:14px}
.review p{font-size:13px;line-height:20px;margin-top:6px}
.review small{display:block;font-size:10px;line-height:13px;margin-top:10px}

.footer-brand{left:0;top:3072px;width:1006px;text-align:center;font-weight:700;font-size:29px;letter-spacing:-1px}
.socials{left:0;top:3123px;width:1006px;display:flex;justify-content:center;gap:18px}
.social{width:28px;height:28px;border:2px solid var(--navy);border-radius:50%}
.foot-col{top:3207px;font-size:13px;line-height:20px}
.foot-phone{left:524px;top:3216px;font-size:13px;font-weight:600}
.foot-hours{left:524px;top:3238px;font-size:9px;color:var(--muted)}
.foot-copy{left:524px;top:3268px;font-size:9px;color:var(--muted)}
</style>
</head>
<body>
<div class="page">
  <header class="abs header">
    <div class="brand">VALKORIN</div>
    <nav class="nav"><span>Produkte</span><span>Fertigung</span><span>Über uns</span><span>Kontakt</span></nav>
  </header>

  <section class="abs hero" role="img" aria-label="Foto: Schweißer bei der Arbeit mit Funkenflug"></section>
  <div class="abs hero-kicker">Willkommen bei Valkorin</div>
  <h1 class="abs hero-title">Meisterhafte<br>Metallverarbeitung<br>für Ihre Visionen</h1>

  <div class="abs band"></div>

  <article class="abs product" style="left:124px">
    <div class="photo" role="img" aria-label="Produktfoto: Maschinengestell für Kälteanlage"></div>
    <h3>Maschinengestelle</h3>
    <p>für spezielle<br>Kälteanlagen</p>
  </article>
  <article class="abs product" style="left:380px">
    <div class="photo" role="img" aria-label="Produktfoto: Spezialgitterbox"></div>
    <h3>Spezialgitterboxen</h3>
    <p>zur Lagerung von<br>Gasen / Flaschen</p>
  </article>
  <article class="abs product" style="left:636px">
    <div class="photo" role="img" aria-label="Produktfoto: Spezialtransportpalette"></div>
    <h3>Spezialtransportpaletten</h3>
    <p>Beispiele für die Lagerung von Gasen / Flaschen</p>
  </article>

  <div class="abs btn all-products">Alle Produkte ansehen</div>

  <article class="abs service" style="left:124px;top:923px">
    <div class="photo" role="img" aria-label="Foto: Stahlkonstruktion mit Funken" style="background:linear-gradient(100deg,#c9ccd0,#5a6a80 50%,#1f3a78)"></div>
    <h3>Stahl- und Palettenbau</h3>
    <p>Wir sind spezialisiert auf die Herstellung von robusten Stahlkonstruktionen und Paletten, die höchsten Ansprüchen gerecht werden.</p>
    <div class="more">Jetzt entdecken</div>
  </article>
  <article class="abs service" style="left:518px;top:923px">
    <div class="photo" role="img" aria-label="Foto: Edelstahlbauteil in einer Anlage" style="background:linear-gradient(120deg,#5b73a4,#8fa0bd 55%,#6f86b0)"></div>
    <h3>Edelstahlbearbeitung</h3>
    <p>Edelstahl verlangt besondere Sorgfalt – wir verarbeiten dieses anspruchsvolle Material zu erstklassigen Produkten.</p>
    <div class="more">Jetzt entdecken</div>
  </article>
  <article class="abs service" style="left:124px;top:1349px">
    <div class="photo" role="img" aria-label="Foto: Maschinenteil in Nahaufnahme" style="background:linear-gradient(120deg,#9db3cf,#26344d 50%,#b8c7d8)"></div>
    <h3>Blechbearbeitung</h3>
    <p>Unsere Fachleute beherrschen die Kunst der Blechbearbeitung und setzen Ihre Ideen präzise in die Realität um.</p>
    <div class="more">Jetzt entdecken</div>
  </article>
  <article class="abs service" style="left:518px;top:1349px">
    <div class="photo" role="img" aria-label="Foto: Arbeiter an einer Fertigungsanlage" style="background:linear-gradient(120deg,#3d5a80,#6d8aae 55%,#2a3e5e)"></div>
    <h3>Mechanische Fertigung</h3>
    <p>Präzision ist der Schlüssel zur mechanischen Fertigung, und Präzision ist unsere Stärke.</p>
    <div class="more">Jetzt entdecken</div>
  </article>

  <section class="abs about">
    <h2>Über Valkorin</h2>
    <article class="abs about-card" style="left:124px">
      <div class="photo" role="img" aria-label="Foto: Lagerhalle mit Regalsystem" style="background:linear-gradient(180deg,#c8cbc8,#8c908a)"></div>
      <h3>Qualität</h3>
      <p>Seit 2001 wachsen wir in Wiesenau bei Lindberg kontinuierlich und leidenschaftlich, um Ihr Experte für hochwertige Metallverarbeitung zu sein.</p>
    </article>
    <article class="abs about-card" style="left:380px">
      <div class="photo" role="img" aria-label="Luftbild: Firmengelände mit Fertigungshalle" style="background:linear-gradient(160deg,#6e7270,#c9cbc8 60%,#7e817e)"></div>
      <h3>Geschichte</h3>
      <p>Unser Team aus hochqualifizierten Fachkräften setzt mit Innovationsgeist und Präzision modernste Maschinen ein, um Ihren Anforderungen gerecht zu werden.</p>
    </article>
    <article class="abs about-card" style="left:636px">
      <div class="photo" role="img" aria-label="Foto: Stahlgitterkonstruktion vor Himmel" style="background:linear-gradient(160deg,#4f5d70,#c5d0dc 55%,#5e6b7c)"></div>
      <h3>Partner</h3>
      <p>Valkorin ist mehr als ein Dienstleister - wir sind Ihr engagierter Partner, der gemeinsam mit Ihnen an der Verwirklichung Ihrer Metallprojekte arbeitet.</p>
    </article>
  </section>

  <div class="abs contact-bottom"></div>
  <h2 class="abs contact-title">Kontakt</h2>
  <div class="abs avatar" role="img" aria-label="Porträtfoto des Inhabers"></div>
  <p class="abs contact-text">Kontaktieren Sie uns, um mehr darüber zu erfahren, wie Valkorin Ihnen helfen kann. Wir freuen uns darauf, Ihr nächstes Metallverarbeitungsprojekt umzusetzen.</p>
  <p class="abs signature">Jonas Brandt<br>Inhaber Valkorin</p>
  <div class="abs email">Ihre E-Mailadresse</div>
  <div class="abs btn send">Absenden</div>

  <article class="abs review" style="left:119px">
    <div class="stars"><svg width="88" height="14" viewBox="0 0 88 14"><g fill="none" stroke="#0b3a73" stroke-width="1.1"><path id="st" d="M7 1l1.8 3.9 4.2.4-3.2 2.8 1 4.1L7 10 3.2 12.2l1-4.1L1 5.3l4.2-.4z"/><use href="#st" x="18"/><use href="#st" x="36"/><use href="#st" x="54"/><use href="#st" x="72"/></g></svg></div>
    <h4>Hervorragender Service</h4>
    <p>Die Mitarbeiter sind sehr freundlich und kompetent und konnten uns in diversen Situationen weiterhelfen</p>
    <small>L. Berger,<br>Nordkälte Technik GmbH</small>
  </article>
  <article class="abs review" style="left:380px">
    <div class="stars"><svg width="88" height="14" viewBox="0 0 88 14"><g fill="none" stroke="#0b3a73" stroke-width="1.1"><use href="#st"/><use href="#st" x="18"/><use href="#st" x="36"/><use href="#st" x="54"/><use href="#st" x="72"/></g></svg></div>
    <h4>Reibungsloser Kauf und excellente Qualität</h4>
    <p>Valkorin liefert Qualität. Wir sind sehr zufrieden.</p>
    <small>K. Wendt,<br>Wendt Anlagenservice</small>
  </article>
  <article class="abs review" style="left:643px">
    <div class="stars"><svg width="88" height="14" viewBox="0 0 88 14"><g fill="none" stroke="#0b3a73" stroke-width="1.1"><use href="#st"/><use href="#st" x="18"/><use href="#st" x="36"/><use href="#st" x="54"/><use href="#st" x="72"/></g></svg></div>
    <h4>Top Service aus Deutschland</h4>
    <p>Die Mitarbeiter sind sehr freundlich und kompetent und konnten uns in diversen Situationen weiterhelfen.</p>
    <small>P. Falk,<br>Falk Lasertechnik</small>
  </article>

  <footer>
    <div class="abs footer-brand">VALKORIN</div>
    <div class="abs socials"><span class="social" aria-label="Social Media"></span><span class="social" aria-label="Social Media"></span><span class="social" aria-label="Social Media"></span></div>
    <div class="abs foot-col" style="left:112px">Halden Stahlwerk<br>Werkstraße 12<br>09999 Musterau<br>Inhaber: Jonas Brandt</div>
    <div class="abs foot-col" style="left:330px">Impressum<br>AGB<br>Datenschutz<br>Jobs</div>
    <div class="abs foot-phone">Telefon 03701 / 555 012 3</div>
    <div class="abs foot-hours">Mo-Fr, 08:30 - 17:30 Uhr</div>
    <div class="abs foot-copy">© 2023 Valkorin, Deutschland</div>
  </footer>
</div>
</body>
</html>
```